Bright Harbor Goods - Product Page

Looking for a design for our product pages to showcase all of the following information in an aesthetically pleasing way. <br/><br/>• Product price per piece & price breaks<br/>• Set up cost <br/>• Additional color cost<br/>• Imprint side <br/>• Product Dimensions<br/><br/>Attached are photos showing ideas we have come up with to display the information. <br/><br/>The link below shows how our product pages is currently laid out. <br/><br/>Link to webpage: https://www.brightharborgoods-example.com/non-woven-reusable-promo-totes.html<br/>

Number of Pages Required

1 page

Colors
33b8a4
33a6d7
3277b5
fece3e
f9a040
a3cd3a

Requirements
Must have
• • Product price per piece & price breaks
• • Set up cost
• • Additional color cost
• • Imprint side
• • Product Dimensions

```html
<!DOCTYPE html>
<html lang="en">
<head>
<meta charset="utf-8">
<title>Bright Harbor Goods – Non-Woven Reusable Promo Totes</title>
<link href="https://fonts.googleapis.com/css2?family=Open+Sans:wght@400;600;700&family=Montserrat:wght@700;800&display=swap" rel="stylesheet">
<style>
:root{
  --teal:#33b8a4;--sky:#33a6d7;--blue:#3277b5;--yellow:#fece3e;--orange:#f9a040;--lime:#a3cd3a;
  --nav:#5aa832;--navy:#1d4f7a;--deep:#15305a;--ink:#333;--muted:#666;--line:#d9d9d9;--star:#f5b400;
}
*{box-sizing:border-box;margin:0;padding:0}
html,body{width:1200px;height:2860px;overflow:hidden}
body{position:relative;font-family:"Open Sans",sans-serif;color:var(--ink);background:#f4f4f4;font-size:14px}
.abs{position:absolute}
/* header */
.header{left:0;top:0;width:1200px;height:100px;background:#fff}
.brand{left:100px;top:40px;font-family:"Open Sans",sans-serif;font-weight:700;font-size:21px;color:var(--nav);line-height:1;display:flex;align-items:center;gap:8px;white-space:nowrap}
.brand .dot{width:14px;height:14px;border-radius:50%;background:var(--orange)}
.rush{left:358px;top:18px;width:72px;height:72px;border-radius:50%;background:#e8452c;border:4px solid #f6a48f;color:#fff;text-align:center;font-weight:700;font-size:14px;line-height:15px;padding-top:14px}
.rush small{display:block;font-size:8px;color:var(--yellow)}
.call{left:478px;top:30px;text-align:center;color:#555;font-size:13px}
.call b{display:block;color:var(--blue);font-size:20px;font-weight:700}
.toplinks{right:100px;top:9px;font-size:11px;color:#555;display:flex;gap:20px}
.social{right:100px;top:32px;display:flex;gap:12px}
.social i,.fsocial i{width:9px;height:9px;border-radius:50%;background:var(--blue);display:block}
.cart{left:712px;top:54px;display:flex;align-items:center;gap:4px}
.cart span{background:var(--nav);color:#fff;font-size:10px;padding:1px 6px;border-radius:2px}
.search{left:763px;top:51px;width:336px;height:28px;border:1px solid var(--line);font-size:10px;color:#777;padding:7px 8px;letter-spacing:.3px}
.search svg{position:absolute;right:6px;top:5px}
.nav{left:0;top:100px;width:1200px;height:40px;background:var(--nav);display:flex;justify-content:center;gap:54px;align-items:center;color:#fff;font-weight:700;font-size:11.5px}
.crumb{left:0;top:140px;width:1200px;height:30px;background:var(--navy);color:#fff;font-size:12.5px;padding:8px 0 0 143px}
.crumb b{font-weight:700}
.hero{left:0;top:170px;width:1200px;height:325px;background:linear-gradient(90deg,#6c8a46,#8fae5a 45%,#b9c478 100%)}
.hero-img{left:40px;top:170px;width:380px;height:325px;background:linear-gradient(160deg,#c24b2c,#3f9a48 55%,#1f9a6c)}
.hero-title{left:505px;top:272px;font-family:"Montserrat",sans-serif;font-weight:800;font-size:54px;line-height:58px;color:#fff;text-shadow:0 2px 4px rgba(0,0,0,.35);white-space:nowrap}
/* sidebar */
.side-title{left:68px;top:534px;font-size:20px;color:#222}
.card{left:72px;width:236px;height:316px;background:#fff;box-shadow:0 1px 4px rgba(0,0,0,.12);text-align:center;font-size:13px;line-height:22px}
.card .pic{margin:20px auto 14px;width:170px;height:150px;border-radius:4px}
.card h4{font-size:15px;font-weight:700}
.card em{font-style:normal;color:var(--sky)}
.stars{color:var(--star);letter-spacing:-1px;font-size:13px}
/* main */
.panel{left:342px;top:540px;width:788px;height:1375px;background:#fff;box-shadow:0 1px 5px rgba(0,0,0,.12)}
.mainpic{left:367px;top:563px;width:296px;height:295px;border:1px solid #eee;background:#fff}
.mainpic div{position:absolute;left:30px;top:28px;width:240px;height:240px;background:linear-gradient(90deg,#d9343a 50%,#c9b48a 50%);border-radius:4px}
.thumb{width:98px;height:93px;border:1px solid #e6e6e6;background:#fff}
.thumb i{position:absolute;left:30px;top:22px;width:38px;height:50px;border-radius:3px}
.sku{left:367px;top:888px;font-size:22px;font-weight:700}
.meta{left:367px;top:934px;font-size:13px;width:700px}
.meta em,.details em{font-style:normal;color:var(--sky)}
.meta .rv{position:absolute;left:303px;top:0;white-space:nowrap}
table.price{width:696px;border-collapse:collapse;font-size:12px;color:#555;background:#fff}
table.price caption{background:linear-gradient(#4b8fcb,var(--blue));color:#fff;font-weight:700;font-size:15px;height:37px;line-height:37px}
table.price td{border:1px solid #cfcfcf;height:36px;text-align:center}
table.price td:first-child{width:147px;text-align:left;padding-left:32px;font-size:15px;color:#222;font-weight:600}
.prod{top:1269px;width:341px;height:214px;font-size:12px}
.prod .head{height:48px;text-align:center;padding-top:5px;font-size:12px;line-height:18px}
.prod .head b{display:block;font-size:16px}
.prod .sub{height:30px;text-align:center;font-weight:700;font-size:15px;line-height:30px;color:#222}
.prod dl{display:grid;grid-template-columns:160px 1fr;row-gap:12px;padding:14px 0 0 53px;font-size:12.5px}
.prod dt{font-weight:700;color:#222}
.btn{top:1524px;width:223px;height:53px;border-radius:27px;color:#fff;font-weight:700;font-size:15px;text-align:center;line-height:53px;letter-spacing:.3px}
.reviews{left:367px;top:1617px;width:696px;height:261px;border:1px solid #e4e4e4}
.reviews .bar{position:absolute;left:8px;top:8px;width:678px;height:44px;background:#f2f2f2;color:var(--blue);font-weight:700;font-size:17px;padding:10px 18px}
.reviews .bar span{position:absolute;right:18px;top:8px;color:#333;font-weight:400}
.reviews p{position:absolute;left:29px;top:76px;width:640px;color:#888;font-size:13px;line-height:25px}
.reviews .by{position:absolute;left:28px;top:164px;font-weight:700;font-size:15px}
.reviews .by em{font-style:normal;color:var(--sky)}
.reviews .all{position:absolute;right:0;bottom:0;width:185px;height:30px;background:#f2f2f2;color:#666;font-size:13px;text-align:center;line-height:30px}
/* details */
.details{left:69px;top:1988px;width:1061px;height:484px;background:#fff;box-shadow:0 1px 5px rgba(0,0,0,.12)}
.tabs{position:absolute;left:5px;top:5px;display:flex;align-items:center;font-weight:700;font-size:13.5px;color:#222}
.tabs .on{background:var(--blue);color:#fff;padding:12px 32px;margin-right:28px}
.tabs span{margin-right:14px}
.spec{position:absolute;left:38px;top:90px;display:grid;grid-template-columns:190px 30px 1fr;row-gap:9px;font-size:13px}
.spec .v{color:#888}
.feat{list-style:none;color:#888}
.feat li{display:flex;align-items:center;gap:18px;height:22.4px;margin-left:-26px}
/* footer */
.footer{left:0;top:2520px;width:1200px;height:300px;background:linear-gradient(180deg,#1c2d55,#15234a)}
.fcol{top:2574px;color:#fff;font-size:10.5px;line-height:20px}
.fcol h5{font-size:14px;font-weight:700;margin-bottom:12px}
.fcol ul{list-style:none;padding-left:8px}
.fbrand{left:64px;top:2574px;width:250px;color:#fff;font-size:10.5px;line-height:14px}
.fbrand b{display:block;font-size:22px;line-height:1;margin-bottom:14px}
.fsocial{display:flex;gap:10px;margin-top:22px}
.fsocial i{background:#fff}
.copy{left:0;top:2820px;width:1200px;height:40px;background:#1a5c93;color:#fff;font-size:10.5px;text-align:center;line-height:40px}
.chat{left:1062px;top:2822px;width:138px;height:38px;background:#8bc34a;border-radius:20px 0 0 20px;color:#fff;font-size:10px;font-weight:700;text-align:right;padding:6px 12px 0 0;line-height:12px}
.chat i{position:absolute;left:2px;top:2px;width:34px;height:34px;border-radius:50%;background:#d7c7b8;border:2px solid #fff}
</style>
</head>
<body>
<header class="header abs"></header>
<div class="brand abs"><span class="dot"></span>Bright Harbor Goods</div>
<div class="rush abs">FREE<br>RUSH<small>Click Here</small></div>
<div class="call abs">Call Us Toll Free:<b>1-800-555-0142</b></div>
<div class="toplinks abs"><span>Home</span><span>About Us</span><span>Contact Us</span><span>Blog</span></div>
<div class="social abs"><i></i><i></i><i></i><i></i><i></i></div>
<div class="cart abs"><svg width="16" height="14" viewBox="0 0 16 14"><path d="M0 1h3l2 8h9l2-6H4" fill="none" stroke="#222" stroke-width="2"/><circle cx="6" cy="12" r="1.5"/><circle cx="13" cy="12" r="1.5"/></svg><span>0</span></div>
<div class="search abs">SEARCH ENTIRE STORE HERE...<svg width="16" height="16" viewBox="0 0 16 16"><circle cx="6.5" cy="6.5" r="4.5" fill="none" stroke="#5aa832" stroke-width="2.4"/><path d="M10 10l4.5 4.5" stroke="#5aa832" stroke-width="2.6"/></svg></div>
<nav class="nav abs"><span>REUSABLE BAGS ▾</span><span>SEED PAPER ▾</span><span>REUSABLE BOTTLES ▾</span><span>LANYARDS ▾</span><span>ECO PROMO ITEMS ▾</span></nav>
<div class="crumb abs">Home &nbsp;&nbsp;»&nbsp;&nbsp; <b>Non-Woven Reusable Promo Totes</b></div>
<section class="hero abs"></section>
<div class="hero-img abs" role="img" aria-label="Green reusable tote filled with fresh vegetables, fruit and bread"></div>
<h1 class="hero-title abs">Non-Woven Reusable<br>Promo Totes</h1>

<h2 class="side-title abs" style="font-weight:400">Recommended Products</h2>
<div class="card abs" style="top:596px"><div class="pic" role="img" aria-label="Green and orange branded totes" style="background:linear-gradient(90deg,#3fbf4a,#7b4fc7 40%,#ea5a3a)"></div><h4>SKU: PP9</h4><em>Size:</em> 16" W x 12" H x 6" D |<br><em>Thickness:</em> 80 GSM<div class="stars">★★★★★</div></div>
<div class="card abs" style="top:930px"><div class="pic" role="img" aria-label="Purple and tan branded totes" style="background:linear-gradient(90deg,#6a4fb3,#d8c59a)"></div><h4>SKU: PP9</h4><em>Size:</em> 16" W x 12" H x 6" D |<br><em>Thickness:</em> 80 GSM<div class="stars">★★★★★</div></div>
<div class="card abs" style="top:1264px"><div class="pic" role="img" aria-label="Blue and red branded totes" style="background:linear-gradient(90deg,#1d78b8,#d9343a)"></div><h4>SKU: PP9</h4><em>Size:</em> 16" W x 12" H x 6" D |<br><em>Thickness:</em> 80 GSM<div class="stars">★★★★★</div></div>
<div class="card abs" style="top:1598px"><div class="pic" role="img" aria-label="Green and tan branded totes" style="background:linear-gradient(90deg,#22a04a,#d8c59a)"></div><h4>SKU: PP9</h4><em>Size:</em> 16" W x 12" H x 6" D |<br><em>Thickness:</em> 80 GSM<div class="stars">★★★★★</div></div>

<main class="panel abs"></main>
<div class="mainpic abs"><div role="img" aria-label="Red and tan branded non-woven totes"></div></div>
<div class="thumb abs" style="left:688px;top:563px"><i style="background:#222"></i></div>
<div class="thumb abs" style="left:794px;top:563px"><i style="background:#1f5a3a"></i></div>
<div class="thumb abs" style="left:899px;top:563px"><i style="background:#2a9a6a"></i></div>
<div class="thumb abs" style="left:1005px;top:563px"><i style="background:#1b8fd0"></i></div>
<div class="thumb abs" style="left:688px;top:664px"><i style="background:#2a2f8f"></i></div>
<div class="thumb abs" style="left:794px;top:664px"><i style="background:#c6b48e"></i></div>
<div class="thumb abs" style="left:899px;top:664px"><i style="background:#22c3b8"></i></div>
<div class="thumb abs" style="left:1005px;top:664px"><i style="background:#2d2f9a"></i></div>
<div class="thumb abs" style="left:688px;top:766px"><i style="background:#f2d94a"></i></div>
<div class="thumb abs" style="left:794px;top:766px"><i style="background:#e0373c"></i></div>

<div class="sku abs">SKU: PP2</div>
<div class="meta abs"><em>Size:</em> 16" W x 12" H x 6" D | <em>Thickness:</em> 80 GSM<span class="rv"><span class="stars">★★★★★</span> &nbsp;38 Review(s) | ✎ Add Review</span></div>

<table class="price abs" style="left:367px;top:991px"><caption>IN-STOCK</caption>
<tr><td>Qty</td><td>1</td><td>100+</td><td>250+</td><td>500+</td><td>1,000+</td><td>2500+</td><td>5,000+</td></tr>
<tr><td>Price</td><td>$0.69</td><td>$1.46</td><td>$1.35</td><td>$1.30</td><td>$1.26</td><td>$1.23</td><td>$1.19</td></tr></table>
<table class="price abs" style="left:367px;top:1126px"><caption>OVERSEAS</caption>
<tr><td>Qty</td><td>1</td><td>100+</td><td>250+</td><td>500+</td><td>1,000+</td><td>2500+</td><td>5,000+</td></tr>
<tr><td>Price</td><td>$0.69</td><td>$1.46</td><td>$1.35</td><td>$1.30</td><td>$1.26</td><td>$1.23</td><td>$1.19</td></tr></table>

<div class="prod abs" style="left:367px;background:#fbf7ea">
  <div class="head" style="background:linear-gradient(var(--yellow),#f6b82c);color:#7a4a00"><b style="color:#1d4f7a">IN-STOCK PRODUCTION</b>Orders of 100pcs or more</div>
  <div class="sub" style="background:#f4edd6">Includes 1 Imprint Color</div>
  <dl><dt>Imprint Size</dt><dd>: 8" W 8" H</dd><dt>Additional Colors</dt><dd>: $0.45 each</dd><dt>Full Color Imprint 300+</dt><dd>: $1.00 each</dd><dt>Set Up Fee</dt><dd>: $45 Per Color</dd></dl>
</div>
<div class="prod abs" style="left:723px;background:#e7fbf8">
  <div class="head" style="background:linear-gradient(#45c6b2,var(--teal));color:#fff"><b>OVERSEAS PRODUCTION</b>Orders of 100pcs or more</div>
  <div class="sub" style="background:#cdf1ea">Free 1 Color,2 Location</div>
  <dl><dt>Imprint Size</dt><dd>: 8" W 8" H</dd><dt>Additional Colors</dt><dd>: $0.45 each</dd><dt>Full Color Imprint 300+</dt><dd>: $1.00 each</dd><dt>Set Up Fee</dt><dd>: $45 Per Color</dd></dl>
</div>

<div class="btn abs" style="left:367px;background:linear-gradient(#b6dc4f,#7fbb2e)">REQUEST A QUOTE</div>
<div class="btn abs" style="left:604px;background:linear-gradient(#fbb257,#f58a26)">BUY NOW</div>
<div class="btn abs" style="left:840px;background:linear-gradient(var(--sky),var(--blue))">ORDER FREE SAMPLE</div>

<div class="reviews abs">
  <div class="bar">Customer Reviews (38)<span>‹ &nbsp;›</span></div>
  <p>Lorem ipsum dolor sit amet, consectetur adipiscing elit, sed do eiusmod tempor incididunt ut labore et dolore magna aliqis ipsumsuspendisse ultrices gras commosuspendisse ultrices gras commo suspendisse ultrices gras commodo viverra maecenas accumsan lacus vel facilisis.</p>
  <div class="by">- Reviews <em>By Dana R</em> &nbsp;&nbsp;<span class="stars">★★★★★</span></div>
  <div class="all">See All Reviews</div>
</div>

<section class="details abs">
  <div class="tabs"><span class="on">DETAILS</span><span>REVIEWS</span><span>/</span><span>ADDITIONAL INFO</span><span>/</span><span>SHIPPING ESTIMATOR</span></div>
  <div class="spec">
    <span>Name</span><span>:</span><span class="v">Non-Woven Reusable Promo Totes</span>
    <span>SKU</span><span>:</span><span class="v">PP2</span>
    <span>Size</span><span>:</span><span class="v">13" W x 14" H x 7" D</span>
    <span>Thickness</span><span>:</span><span class="v">100 GSM</span>
    <span>Available Colors</span><span>:</span><span class="v">Black, Hunter Green, Kelly Green, Lime Green, Maui Blue, Navy Blue, Purple, Red, Royal Blue, Tan, Teal &amp; Yellow</span>
    <span>Imprint Area</span><span>:</span><span class="v">8" W x 8" H</span>
    <span>Key Features</span><span></span>
    <ul class="feat">
      <li><svg width="12" height="12"><circle cx="6" cy="6" r="6" fill="#33b8a4"/><path d="M3 6l2 2 4-4" stroke="#fff" stroke-width="1.6" fill="none"/></svg>Spacious Main Compartment, 1274 Cubic Inches</li>
      <li><svg width="12" height="12"><circle cx="6" cy="6" r="6" fill="#33b8a4"/><path d="M3 6l2 2 4-4" stroke="#fff" stroke-width="1.6" fill="none"/></svg>22” Carry Straps</li>
      <li><svg width="12" height="12"><circle cx="6" cy="6" r="6" fill="#33b8a4"/><path d="M3 6l2 2 4-4" stroke="#fff" stroke-width="1.6" fill="none"/></svg>Made from 100 GSM Non-Woven Polypropylene</li>
      <li><svg width="12" height="12"><circle cx="6" cy="6" r="6" fill="#33b8a4"/><path d="M3 6l2 2 4-4" stroke="#fff" stroke-width="1.6" fill="none"/></svg>Eco-Friendly and 100% Recyclable</li>
      <li><svg width="12" height="12"><circle cx="6" cy="6" r="6" fill="#33b8a4"/><path d="M3 6l2 2 4-4" stroke="#fff" stroke-width="1.6" fill="none"/></svg>Removable Hard Bottom Insert at the Base</li>
      <li><svg width="12" height="12"><circle cx="6" cy="6" r="6" fill="#33b8a4"/><path d="M3 6l2 2 4-4" stroke="#fff" stroke-width="1.6" fill="none"/></svg>5 Day Standard Production / RUSH service available</li>
      <li><svg width="12" height="12"><circle cx="6" cy="6" r="6" fill="#33b8a4"/><path d="M3 6l2 2 4-4" stroke="#fff" stroke-width="1.6" fill="none"/></svg>10 Day Production for Full Color Artwork</li>
      <li><svg width="12" height="12"><circle cx="6" cy="6" r="6" fill="#33b8a4"/><path d="M3 6l2 2 4-4" stroke="#fff" stroke-width="1.6" fill="none"/></svg>8” Wide x 8” High Imprint Area</li>
      <li><svg width="12" height="12"><circle cx="6" cy="6" r="6" fill="#33b8a4"/><path d="M3 6l2 2 4-4" stroke="#fff" stroke-width="1.6" fill="none"/></svg>Made From Recycled Content</li>
    </ul>
  </div>
</section>

<footer class="footer abs" role="img" aria-label="Dark collage of printed promotional bags"></footer>
<div class="fbrand abs"><b>Bright Harbor Goods</b>Bright Harbor Goods is an eco-friendly company that specializes in manufacturing custom bags. BHG was founded in 2009 and has strived to make the world a better place ever since.<div class="fsocial"><i></i><i></i><i></i><i></i><i></i></div></div>
<div class="fcol abs" style="left:330px"><h5>USEFUL LINKS</h5><ul><li>Customer Service</li><li>Our Story</li><li>Site Map</li><li>FTC Disclosure</li><li>Privacy Policy</li><li>Contact Us</li><li>Art &amp; Imprint Policy</li><li>Free Rush</li></ul></div>
<div class="fcol abs" style="left:595px"><h5>WHY BUY FROM US</h5><ul><li>Reusable Bag Stats</li><li>Best Price Guarantee</li><li>Return &amp; Refund Policy</li><li>Shipping Policy</li><li>In-Stock &amp; Custom Production</li><li>Frequently Asked Questions</li></ul></div>
<div class="fcol abs" style="left:860px;line-height:13px"><h5 style="line-height:20px">ADDRESS</h5>480 Harbor Way, Suite 12<br>Bayview, FL 33000<br><br><br>Phone: 1-800-555-0142<br><br><br>Email: hello@brightharborgoods-example.com</div>
<div class="copy abs">© 2020 BrightHarborGoods.com</div>
<div class="chat abs"><i></i>LEAVE<br>A MESSAGE</div>
</body>
</html>
```